Quorva - corporate Business Card

We need a good look and innovative business card for a new start up company based in Los Angeles called "Quorva". We are in a payment business, including payment card, app, and ewallet. We are expert in online payment and Card not present (CNP) transaction.
We need an innovative, modern business card.

Our logo font is Aero Matics

Target Market(s)

Startup - Bank - Online Payment - Card Manufacturing

Industry/Entity Type

Startup

Contact Information for Business Card

phone: 555 014 7396 - Address: 4172 Marlowe blvd, Ashvale, NV 89417

Requirements
Must have
• Message: innovative, professional, expert, high tech, trust, online payment expert, security
Nice to have
• no comment
Should not have
• no Comment

```html
<!DOCTYPE html>
<html lang="en">
<head>
<meta charset="utf-8">
<title>Quorva – Business Card</title>
<link rel="stylesheet" href="https://fonts.googleapis.com/css2?family=Montserrat:wght@600;800&family=Open+Sans:wght@400&display=swap">
<style>
  :root {
    --stage: #ecebe9;
    --card-red: #b51f2e;
    --card-red-dark: #9e1826;
    --text-light: #ffffff;
    --disc-light: #f4f4f4;
    --disc-mid: #d9d9d9;
    --disc-shade: #bdbdbd;
  }
  * { box-sizing: border-box; margin: 0; padding: 0; }
  html, body {
    width: 1200px;
    height: 900px;
    overflow: hidden;
    background: var(--stage);
  }
  .business-card {
    position: absolute;
    left: 180px;
    top: 191px;
    width: 840px;
    height: 517px;
    border-radius: 20px;
    background: linear-gradient(160deg, var(--card-red) 0%, var(--card-red) 70%, var(--card-red-dark) 100%);
    box-shadow: 0 10px 30px rgba(0,0,0,0.18);
    color: var(--text-light);
    font-family: "Open Sans", Arial, sans-serif;
  }
  .holder {
    position: absolute;
    left: 39px;
    top: 68px;
  }
  .holder-name {
    font-family: "Montserrat", Arial, sans-serif;
    font-weight: 800;
    font-size: 25px;
    letter-spacing: 0.2px;
    line-height: 1;
  }
  .holder-role {
    margin-top: 6px;
    font-size: 20px;
    line-height: 1;
  }
  .contact-list {
    position: absolute;
    left: 39px;
    top: 331px;
    list-style: none;
    font-size: 21px;
    line-height: 32px;
  }
  .contact-item {
    display: flex;
    align-items: flex-start;
  }
  .contact-icon {
    width: 18px;
    height: 18px;
    margin-top: 7px;
    margin-right: 12px;
    flex: none;
    fill: var(--text-light);
  }
  .brand-disc {
    position: absolute;
    left: 393px;
    top: 62px;
    width: 392px;
    height: 392px;
    border-radius: 50%;
    background: radial-gradient(circle at 35% 30%, var(--disc-light) 0%, var(--disc-mid) 60%, var(--disc-shade) 100%);
  }
  .brand-dot {
    position: absolute;
    left: 135px;
    top: 73px;
    width: 122px;
    height: 122px;
    border-radius: 50%;
    background: var(--card-red);
  }
  .brand-name {
    position: absolute;
    left: 0;
    right: 0;
    top: 208px;
    text-align: center;
    font-family: "Montserrat", Arial, sans-serif;
    font-weight: 600;
    font-size: 70px;
    line-height: 1;
    color: var(--card-red);
  }
</style>
</head>
<body>
  <main class="business-card">
    <header class="holder">
      <h1 class="holder-name">DANIEL HARROW</h1>
      <p class="holder-role">Managing Director</p>
    </header>

    <ul class="contact-list">
      <li class="contact-item">
        <svg class="contact-icon" viewBox="0 0 24 24" aria-hidden="true">
          <path d="M6.6 10.8a15.2 15.2 0 0 0 6.6 6.6l2.2-2.2a1 1 0 0 1 1-.25 11.4 11.4 0 0 0 3.6.57 1 1 0 0 1 1 1V20a1 1 0 0 1-1 1A17 17 0 0 1 3 4a1 1 0 0 1 1-1h3.5a1 1 0 0 1 1 1c0 1.25.2 2.450.57 3.57a1 1 0 0 1-.25 1z"/>
        </svg>
        <span>555 014 7396</span>
      </li>
      <li class="contact-item">
        <svg class="contact-icon" viewBox="0 0 24 24" aria-hidden="true">
          <circle cx="12" cy="12" r="10"/>
          <path d="M7 8c2 0 3 1 3 3s2 2 2 4-1 3-1 5M14 4c0 2 1 3 3 3s3 2 3 3" stroke="#b51f2e" stroke-width="1.8" fill="none"/>
        </svg>
        <span>www.quorva.com</span>
      </li>
      <li class="contact-item">
        <svg class="contact-icon" viewBox="0 0 24 24" aria-hidden="true">
          <path d="M12 2a7 7 0 0 0-7 7c0 5.2 7 13 7 13s7-7.8 7-13a7 7 0 0 0-7-7zm0 9.5A2.5 2.5 0 1 1 12 6.5a2.5 2.5 0 0 1 0 5z"/>
        </svg>
        <span>4172 Marlowe blvd<br>Ashvale, NV 89417</span>
      </li>
    </ul>

    <div class="brand-disc">
      <div class="brand-dot"></div>
      <p class="brand-name">quorva</p>
    </div>
  </main>
</body>
</html>
```